www.marvenholt.com

Updating website so looks futristic but yet business like and easy to navigate, essentially a good landing page with a cool picture summing up what we do, and links to the following pages, all other pages on site to be updated, Exclusive Distributor of Brisk Forge Unique Fitness Equipment Products in UK & Ireland, www.crestvolley.co.uk Exclusive Partners & Distributors Of Crest Volley - Obstacle Races - Obstacle Hire - Obstacle Training - Adventure Events, www.goplumwick.co.uk Adventures That Inspire. We also Health Club / Facillity Consultancy

```html
<!DOCTYPE html>
<html lang="en">
<head>
<meta charset="utf-8">
<title>Marvenholt – Health, Wellness, Fitness, Consultants</title>
<link rel="stylesheet" href="https://fonts.googleapis.com/css2?family=Marcellus+SC&family=Raleway:wght@400;500;600;700;800&display=swap">
<style>
:root{
  --yellow:#e3c000;
  --yellow-deep:#d1b000;
  --ink:#1f1f1f;
  --charcoal:#2a2a2a;
  --grey:#6b6b6b;
  --light:#f4f4f4;
  --white:#ffffff;
  --footer:#1b1b1b;
}
*{box-sizing:border-box;margin:0;padding:0}
html,body{width:1200px;height:4072px;overflow:hidden}
body{font-family:"Raleway",sans-serif;color:var(--ink);background:var(--white);position:relative}
.serif{font-family:"Marcellus SC",serif}
.hl{color:var(--yellow)}
.abs{position:absolute}

/* header */
.site-header{position:absolute;top:0;left:0;width:1200px;height:141px;background:var(--white);box-shadow:0 2px 8px rgba(0,0,0,.08);z-index:2}
.social{position:absolute;left:90px;top:8px;display:flex;gap:10px}
.social span{width:20px;height:20px;border-radius:50%;background:var(--yellow);display:block}
.top-contact{position:absolute;left:600px;top:8px;font-size:15px;color:var(--ink);display:flex;align-items:center;gap:10px}
.brand-tab{position:absolute;right:0;top:0;width:280px;height:42px;background:var(--charcoal);color:var(--white);font-family:"Marcellus SC",serif;font-size:22px;display:flex;align-items:center;justify-content:center;clip-path:polygon(30px 0,100% 0,100% 100%,0 100%)}
.logo{position:absolute;left:88px;top:56px}
.logo .name{font-family:"Marcellus SC",serif;font-size:38px;line-height:1;color:var(--ink)}
.logo .tag{font-family:"Marcellus SC",serif;font-size:15px;color:var(--ink);margin-top:4px}
.main-nav{position:absolute;left:416px;top:73px;display:flex;gap:0;font-size:15px;font-weight:500}
.main-nav a{color:var(--ink);text-decoration:none;height:42px;line-height:42px;padding:0 15px;letter-spacing:.5px}
.main-nav a.active{background:var(--charcoal);color:var(--white);padding:0 20px;margin-right:10px}

/* hero */
.hero{position:absolute;top:141px;left:0;width:1200px;height:538px}
.hero-photo{position:absolute;inset:0;background:linear-gradient(100deg,#e9e9e9 0%,#cfcfcf 40%,#9a9a9a 70%,#c8c8c8 100%)}
.hero h1{position:absolute;left:76px;top:160px;font-family:"Raleway",sans-serif;font-weight:800;font-size:72px;color:#111}
.hero .sub{position:absolute;left:80px;top:262px;font-family:"Marcellus SC",serif;font-size:30px;color:var(--white);text-shadow:0 1px 3px rgba(0,0,0,.5)}
.hero .btns{position:absolute;left:80px;top:330px;display:flex;gap:14px}
.btn{display:inline-flex;align-items:center;justify-content:center;height:62px;padding:0 24px;font-family:"Marcellus SC",serif;font-size:22px;text-decoration:none}
.btn-yellow{background:var(--yellow);color:var(--white)}
.btn-dark{background:var(--charcoal);color:var(--white)}
.slide-arrow{position:absolute;top:248px;width:56px;height:56px;border-radius:50%;border:2px solid var(--white);background:rgba(0,0,0,.2)}
.slide-arrow.left{left:12px}.slide-arrow.right{right:12px}

/* join bar */
.join-bar{position:absolute;top:679px;left:0;width:1200px;height:108px;background:var(--yellow)}
.join-bar h3{position:absolute;left:82px;top:38px;font-family:"Marcellus SC",serif;font-weight:400;font-size:26px;color:var(--ink)}
.field{background:var(--white);height:52px;font-size:14px;color:var(--grey);padding:0 14px;display:flex;align-items:center}
.join-bar .field{position:absolute;top:28px}
.btn-submit{background:var(--charcoal);color:var(--white);font-family:"Marcellus SC",serif;font-size:22px;display:flex;align-items:center;justify-content:center;height:52px}

/* welcome */
.welcome-photo{position:absolute;left:76px;top:828px;width:424px;height:258px;background:radial-gradient(ellipse at 50% 55%,#d8d8d8 0%,#f3f3f3 70%,#fff 100%)}
.welcome h2{position:absolute;left:538px;top:842px;font-family:"Marcellus SC",serif;font-weight:400;font-size:46px}
.welcome p{position:absolute;left:542px;top:900px;width:580px;font-size:15px;line-height:25px;color:var(--grey)}
.welcome .btn{position:absolute;left:543px;top:1015px;height:58px;width:190px}
.divider{position:absolute;left:300px;top:1132px;width:600px;height:6px;border-radius:50%;background:radial-gradient(ellipse at center,rgba(0,0,0,.18),rgba(0,0,0,0) 70%)}

/* section titles */
.section-title{position:absolute;left:0;width:1200px;text-align:center;font-family:"Marcellus SC",serif;font-weight:400;font-size:48px;color:var(--ink)}
.section-sub{position:absolute;left:0;width:1200px;text-align:center;font-size:17px;color:var(--ink)}

/* expertise */
.expert-card{position:absolute;top:1295px;width:334px;height:293px}
.expert-card .photo{height:225px}
.expert-card .label{height:68px;background:var(--yellow);font-family:"Marcellus SC",serif;font-size:24px;display:flex;align-items:center;justify-content:center;color:var(--ink)}

/* team */
.team{position:absolute;top:1648px;left:0;width:1200px;height:312px;background:var(--yellow)}
.team-photo{position:absolute;left:0;top:0;width:584px;height:312px;background:linear-gradient(90deg,#4a6b8a 0%,#7d95ad 55%,#5b6e80 100%)}
.team h3{position:absolute;left:633px;top:44px;font-family:"Marcellus SC",serif;font-weight:400;font-size:30px;color:var(--ink)}
.team p{position:absolute;left:636px;top:90px;width:500px;font-size:14px;line-height:25px;color:var(--white)}
.team .btn{position:absolute;left:636px;top:226px;height:52px;width:190px;font-size:21px}
.dots{position:absolute;right:30px;top:96px;display:flex;flex-direction:column;gap:26px}
.dots span{width:20px;height:20px;border-radius:50%;background:var(--white);display:block}
.dots span.on{background:var(--charcoal)}

/* testimonials */
.quote-card{position:absolute;top:2099px;width:524px;height:160px;background:var(--white);box-shadow:0 2px 10px rgba(0,0,0,.15);padding:34px 44px;font-size:15px;line-height:27px;text-align:center;color:var(--ink)}
.quote-card.faded{opacity:.3}
.quote-card .mark{position:absolute;font-size:44px;color:var(--yellow);font-family:Georgia,serif;line-height:1}
.quote-card::after{content:"";position:absolute;left:50px;bottom:-18px;border-left:18px solid transparent;border-right:18px solid transparent;border-top:18px solid var(--white)}
.client{position:absolute;top:2292px;display:flex;align-items:center;gap:20px}
.client .avatar{width:70px;height:70px;border-radius:50%;background:var(--charcoal)}
.client .who{font-size:14px;color:var(--grey)}
.client .who b{display:block;font-family:"Marcellus SC",serif;font-weight:400;font-size:18px;color:var(--yellow)}
.stars{position:absolute;top:2295px;left:718px;display:flex;gap:6px}

/* video */
.video{position:absolute;top:2430px;left:0;width:1200px;height:413px;background:linear-gradient(180deg,#1d1d1d 0%,#3a3a3a 50%,#1a1a1a 100%)}
.video h2{position:absolute;top:92px;left:0;width:1200px;text-align:center;font-family:"Marcellus SC",serif;font-weight:400;font-size:46px;color:var(--white)}
.play{position:absolute;left:540px;top:179px}

/* events */
.event-card{position:absolute;top:2973px;width:508px;height:353px;background:var(--white);box-shadow:0 1px 6px rgba(0,0,0,.15)}
.event-card .photo{height:209px}
.event-card .date{position:absolute;left:14px;top:185px;height:48px;width:200px;background:var(--yellow);font-family:"Marcellus SC",serif;font-size:24px;display:flex;align-items:center;justify-content:center}
.event-card p{position:absolute;left:14px;top:250px;width:470px;font-size:14px;line-height:24px;color:var(--ink)}
.event-card svg{position:absolute;right:14px;bottom:14px}

/* business */
.business{position:absolute;top:3388px;left:76px;width:1048px;height:256px;background:linear-gradient(90deg,#d9b800 0%,#ecd12a 50%,#d4b300 100%)}
.business h2{position:absolute;top:44px;left:0;width:1048px;text-align:center;font-family:"Marcellus SC",serif;font-weight:400;font-size:46px;color:var(--ink)}
.business .lead{position:absolute;top:100px;left:0;width:1048px;text-align:center;font-size:17px;color:var(--ink)}
.business .field{position:absolute;top:147px;width:208px}
.business .btn-submit{position:absolute;top:147px;left:876px;width:158px}

/* footer */
.site-footer{position:absolute;top:3701px;left:0;width:1200px;height:304px;background:var(--footer);color:var(--white)}
.foot-logo{position:absolute;left:90px;top:100px;text-align:center}
.foot-logo .name{font-family:"Marcellus SC",serif;font-size:36px}
.foot-logo .tag{font-family:"Marcellus SC",serif;font-size:15px;margin-top:2px}
.foot-logo .social{position:static;justify-content:center;margin-top:14px}
.foot-col{position:absolute;top:36px}
.foot-col h4{font-family:"Marcellus SC",serif;font-weight:400;font-size:17px;color:var(--yellow);margin-bottom:10px}
.foot-col ul{list-style:none;font-size:13px;line-height:29px}
.foot-col li.on{color:var(--yellow)}
.contact-row{display:flex;gap:14px;font-size:13px;line-height:22px;margin-bottom:14px;width:230px}
.contact-row svg{flex:none;margin-top:3px}
.thumbs{display:grid;grid-template-columns:repeat(3,80px);gap:6px}
.thumbs span{height:73px;display:block}
.view-all{display:block;text-align:right;font-size:13px;color:var(--yellow);text-decoration:underline;margin-top:10px;width:252px}
.copyright{position:absolute;top:4005px;left:0;width:1200px;height:67px;background:var(--yellow);font-size:14px;display:flex;align-items:center;justify-content:center;color:var(--ink)}
</style>
</head>
<body>

<header class="site-header">
  <div class="social"><span></span><span></span></div>
  <div class="top-contact">
    <svg width="18" height="18" viewBox="0 0 24 24"><path fill="#1f1f1f" d="M6.6 10.8a15 15 0 0 0 6.6 6.6l2.2-2.2c.3-.3.7-.4 1-.2 1.1.4 2.3.6 3.6.6.6 0 1 .4 1 1V20c0 .6-.4 1-1 1A17 17 0 0 1 3 4c0-.6.4-1 1-1h3.5c.6 0 1 .4 1 1 0 1.3.2 2.5.6 3.6.1.3 0 .7-.2 1z"/></svg>
    <span>07-555-010-482 &nbsp;or&nbsp; 01-555-019-330</span>
  </div>
  <div class="brand-tab">Brisk Forge</div>
  <div class="logo"><div class="name">Marvenholt</div><div class="tag">Health, Wellness, Fitness, Consultants</div></div>
  <nav class="main-nav">
    <a class="active">HOME</a><a>HEALTH</a><a>WELLNESS</a><a>FITNESS</a><a>OUR TEAM</a><a>TESTIMONIALS</a><a>CONTACT</a>
  </nav>
</header>

<section class="hero">
  <div class="hero-photo" role="img" aria-label="Woman doing a push-up on a mat in a bright gym, trainer in the background"></div>
  <h1>Ready To Start ?</h1>
  <div class="sub">Health, Wellness, Fitness, Consultants</div>
  <div class="btns"><a class="btn btn-yellow">JOIN US NOW</a><a class="btn btn-dark">FREE CONSULTANCY</a></div>
  <div class="slide-arrow left"></div><div class="slide-arrow right"></div>
</section>

<section class="join-bar">
  <h3>Join Our Health Club</h3>
  <div class="field" style="left:380px;width:272px">Enter Name*</div>
  <div class="field" style="left:662px;width:270px">Enter Email*</div>
  <div class="btn-submit abs" style="left:945px;top:28px;width:165px">SUBMIT</div>
</section>

<section class="welcome">
  <div class="welcome-photo" role="img" aria-label="Athlete holding a push-up position"></div>
  <h2>Welcome To <span class="hl">Marvenholt</span></h2>
  <p>Marvenholt are leading consultants to the Health, Wellness and Fitness industry, with over 25 years experience working with some of the biggest global brands from equipment providers and facility operators. To mass participation events and obstacle course races.</p>
  <a class="btn btn-dark">LEARN MORE</a>
  <div class="divider"></div>
</section>

<section class="expertise">
  <h2 class="section-title" style="top:1180px">We Are <span class="hl">Expert In</span></h2>
  <div class="section-sub" style="top:1248px">We Provide You</div>
  <div class="expert-card" style="left:76px"><div class="photo" role="img" aria-label="Group stretching outdoors on grass" style="background:linear-gradient(160deg,#a6c27a,#e4e6d6)"></div><div class="label">Health</div></div>
  <div class="expert-card" style="left:434px"><div class="photo" role="img" aria-label="Woman resting on a beach at sunset" style="background:linear-gradient(170deg,#c9a06a,#e8cfa4 55%,#8a7a66)"></div><div class="label">Wellness</div></div>
  <div class="expert-card" style="left:790px"><div class="photo" role="img" aria-label="Class training with kettlebells" style="background:linear-gradient(160deg,#5c5c5c,#b5b5b5)"></div><div class="label">Fitness</div></div>
</section>

<section class="team">
  <div class="team-photo" role="img" aria-label="Portrait of a team member in a suit"></div>
  <h3>The Team @ Marvenholt</h3>
  <p>Marvenholt long term success depends on the talents, commitment and shared values of our people. Marvenholt is made of a unique hand picked team that will ensure the best possible service is delivered, as a company we're passionate about delivering the best for our clients so we employ and partner with the best people.</p>
  <a class="btn btn-dark">LEARN MORE</a>
  <div class="dots"><span></span><span></span><span class="on"></span><span></span></div>
</section>

<section class="testimonials">
  <h2 class="section-title" style="top:2010px">What Our <span class="hl">Client Say</span></h2>
  <div class="quote-card faded" style="left:-217px">Marvenholt first collaborated in 2015 and showed impeccable drive, commitment, passion throughout our partnership.</div>
  <div class="quote-card" style="left:340px">
    <span class="mark" style="left:16px;top:18px">&ldquo;</span>
    Halvard Ridgeline Run and Marvenholt first collaborated in 2015. Tomas and the Marvenholt team have showed impeccable drive, commitment, passion and integrity throughout our partnership.
    <span class="mark" style="right:90px;bottom:6px">&rdquo;</span>
  </div>
  <div class="quote-card faded" style="left:905px">Halvard Ridgeline Run and Marvenholt first collaborated. Tomas and the team have showed passion throughout.</div>
  <div class="client" style="left:363px"><div class="avatar"></div><div class="who"><b>– Rowan Calder</b>Ridgeline Run CEO &amp; Founder of Ridgeline Run</div></div>
  <div class="client faded" style="left:928px;opacity:.3"><div class="avatar" style="background:#4a8fd0"></div><div class="who"><b>Rowan Calder</b>Civic Care CEO &amp; Founder</div></div>
  <div class="stars">
    <svg width="140" height="22" viewBox="0 0 140 22"><g fill="none" stroke="#e3c000" stroke-width="1.6">
      <path id="st" d="M11 1l3 6.5 7 .8-5.2 4.8 1.4 7L11 16.6 4.8 20.1l1.4-7L1 8.3l7-.8z"/>
      <use href="#st" x="28"/><use href="#st" x="56"/><use href="#st" x="84"/><use href="#st" x="112"/></g></svg>
  </div>
</section>

<section class="video" role="img" aria-label="Dim background of an athlete training in a gym">
  <h2>Watch Marvenholt <span class="hl">Videos</span></h2>
  <svg class="play" width="120" height="120" viewBox="0 0 120 120"><circle cx="60" cy="60" r="56" fill="rgba(227,192,0,.35)" stroke="#e3c000" stroke-width="5"/><path d="M48 38l34 22-34 22z" fill="#e3c000"/></svg>
</section>

<section class="events">
  <h2 class="section-title" style="top:2890px">Marvenholt <span class="hl">Events</span></h2>
  <div class="event-card" style="left:76px">
    <div class="photo" role="img" aria-label="Indoor cycling class in a fitness studio" style="background:linear-gradient(180deg,#9fc6e6,#d9d0c4 60%,#a39582)"></div>
    <div class="date">11 October 2017</div>
    <p>Lorem Ipsum is simply dummy text of the printing and typesetting industry. Lorem Ipsum has been the industry's standard dummy text ever since the 1500s, when an unknown printer took.</p>
    <svg width="34" height="16" viewBox="0 0 34 16"><path d="M0 8h30M24 2l7 6-7 6" stroke="#e3c000" stroke-width="3" fill="none"/></svg>
  </div>
  <div class="event-card" style="left:614px">
    <div class="photo" role="img" aria-label="Runners splashing through a muddy obstacle course" style="background:linear-gradient(180deg,#b7bcc0,#8d8a72 60%,#6d6652)"></div>
    <div class="date">11 October 2017</div>
    <p>Lorem Ipsum is simply dummy text of the printing and typesetting industry. Lorem Ipsum has been the industry's standard dummy text ever since the 1500s, when an unknown printer took.</p>
    <svg width="34" height="16" viewBox="0 0 34 16"><path d="M0 8h30M24 2l7 6-7 6" stroke="#e3c000" stroke-width="3" fill="none"/></svg>
  </div>
</section>

<section class="business">
  <h2>Build Your <span style="color:#fff">Business Today</span></h2>
  <div class="lead">Need a free quote, or have a question? Get in touch!</div>
  <div class="field" style="left:14px">Name *</div>
  <div class="field" style="left:230px">Email *</div>
  <div class="field" style="left:446px">Subject *</div>
  <div class="field" style="left:662px">Message *</div>
  <div class="btn-submit">SUBMIT</div>
</section>

<footer class="site-footer">
  <div class="foot-logo">
    <div class="name">Marvenholt</div>
    <div class="tag">Health, Wellness, Fitness, Consultants</div>
    <div class="social"><span></span><span></span></div>
  </div>
  <div class="foot-col" style="left:345px">
    <h4>Sitemap</h4>
    <ul><li class="on">» Home</li><li>» Health</li><li>» Wellness</li><li>» Fitness</li><li>» Our Team</li><li>» Testimonials</li><li>» Contact Us</li></ul>
  </div>
  <div class="foot-col" style="left:605px">
    <h4>Contact Us</h4>
    <div class="contact-row"><svg width="18" height="18" viewBox="0 0 24 24"><path fill="#e3c000" d="M12 2a7 7 0 0 0-7 7c0 5 7 13 7 13s7-8 7-13a7 7 0 0 0-7-7zm0 9.5A2.5 2.5 0 1 1 12 6.5a2.5 2.5 0 0 1 0 5z"/></svg><span>The Mews , Eastbrook UK &amp; Ireland</span></div>
    <div class="contact-row"><svg width="18" height="18" viewBox="0 0 24 24"><path fill="#e3c000" d="M6.6 10.8a15 15 0 0 0 6.6 6.6l2.2-2.2c.3-.3.7-.4 1-.2 1.1.4 2.3.6 3.6.6.6 0 1 .4 1 1V20c0 .6-.4 1-1 1A17 17 0 0 1 3 4c0-.6.4-1 1-1h3.5c.6 0 1 .4 1 1 0 1.3.2 2.5.6 3.6.1.3 0 .7-.2 1z"/></svg><span>07-555-010-482 &nbsp;or<br>01-555-019-330</span></div>
    <div class="contact-row"><svg width="18" height="18" viewBox="0 0 24 24"><rect x="2" y="5" width="20" height="14" fill="none" stroke="#e3c000" stroke-width="2"/><path d="M2 6l10 7 10-7" fill="none" stroke="#e3c000" stroke-width="2"/></svg><span>hello@marvenholt.com</span></div>
    <div class="contact-row"><svg width="18" height="18" viewBox="0 0 24 24"><circle cx="12" cy="12" r="9" fill="none" stroke="#e3c000" stroke-width="2"/><path d="M3 12h18M12 3c3 3 3 15 0 18M12 3c-3 3-3 15 0 18" fill="none" stroke="#e3c000" stroke-width="1.5"/></svg><span>www.marvenholt.com</span></div>
  </div>
  <div class="foot-col" style="left:874px">
    <h4>What We Do</h4>
    <div class="thumbs" role="img" aria-label="Gallery of fitness activity photos">
      <span style="background:#8fa6b8"></span><span style="background:#c9a07a"></span><span style="background:#9a9a9a"></span>
      <span style="background:#7f8f9f"></span><span style="background:#b89a84"></span><span style="background:#a3b2c0"></span>
    </div>
    <a class="view-all">View All</a>
  </div>
</footer>
<div class="copyright">©Marvenholt - 2017 All Right Reserved.</div>

</body>
</html>
```